TK Homes - Stone Dorf Design

Looking for a double sides design, 1 side for my realestate and the other for home building. ( TK Homes on 1 side, Stone Dorf card on the other Side
Side 1 - Marek Tove ~ Vox Realty logo and Company ( the Property quarter )
Marek Tove
Marek@Marektove.example
IG - Marek_Bzq_Realtor
FB - marekt
Cell - 5558130467
3847 61 St Nw

Side 2
Marek Tove
5558130467
IG - Stonedorf_Bzq
Stonedorfdev@mailbox.example

Target Market(s)

Home buyers/ sellers

Industry/Entity Type

Home builders - Realestate

Contact Information for Business Card

Above

Requirements
Must have
• Black OR White background - my information -

```html
<!DOCTYPE html>
<html lang="en">
<head>
<meta charset="utf-8">
<title>Marek Tove – Business Cards</title>
<link rel="stylesheet" href="https://fonts.googleapis.com/css2?family=Tinos:wght@400;700&display=swap">
<style>
  :root {
    --stage: #242424;
    --card: #1d1d20;
    --card-edge: #2a2a2e;
    --blue: #1474c4;
    --gold: #f7c936;
    --ink: #f2f2f2;
    --emboss: #141416;
  }
  * { box-sizing: border-box; margin: 0; padding: 0; }
  html, body {
    width: 1200px; height: 780px; overflow: hidden;
    background: var(--stage);
    font-family: "Tinos", "Times New Roman", serif;
  }
  .stage { position: relative; width: 1200px; height: 780px; }
  .card {
    position: absolute;
    width: 560px; height: 320px;
    background: var(--card);
    border: 1px solid var(--card-edge);
    box-shadow: 0 18px 40px rgba(0,0,0,.55);
    overflow: hidden;
  }
  .card--builder { left: 60px; top: 60px; }
  .card--realty { left: 580px; top: 400px; }

  .emboss-mark {
    position: absolute; right: 40px; top: 40px;
    width: 200px; height: 200px;
    background: var(--emboss);
    box-shadow: inset 2px 2px 6px rgba(0,0,0,.6), inset -1px -1px 3px rgba(255,255,255,.04);
  }

  .brand {
    position: absolute; left: 40px; top: 36px;
    font-weight: 700; font-size: 34px; letter-spacing: 1px;
    color: var(--blue); text-transform: uppercase;
  }
  .card--realty .brand { font-size: 28px; }

  .identity {
    position: absolute; left: 0; top: 110px;
    padding-left: 44px;
  }
  .identity__bar {
    position: absolute; left: 14px; top: 8px;
    width: 16px; height: 52px; background: var(--blue);
  }
  .card--realty .identity { top: 96px; }
  .name { font-weight: 700; font-size: 32px; line-height: 1; }
  .name__first { color: var(--blue); }
  .name__last { color: var(--gold); }
  .role { font-weight: 700; font-size: 16px; color: var(--ink); margin-top: 2px; }

  .contacts {
    position: absolute; left: 70px; top: 200px;
    list-style: none; color: var(--ink); font-size: 15px; line-height: 1.35;
  }
  .card--realty .contacts { top: 168px; font-size: 14px; line-height: 1.3; }
  .contacts li { display: flex; align-items: center; gap: 8px; }
  .contacts svg { width: 13px; height: 13px; fill: var(--blue); flex: none; }
</style>
</head>
<body>
<main class="stage">

  <section class="card card--builder" aria-label="Stone Dorf business card">
    <div class="emboss-mark" aria-hidden="true"></div>
    <div class="brand">Stone Dorf</div>
    <div class="identity">
      <span class="identity__bar"></span>
      <p class="name"><span class="name__first">Marek</span> <span class="name__last">Tove</span></p>
      <p class="role">Director</p>
    </div>
    <ul class="contacts">
      <li><svg viewBox="0 0 24 24"><path d="M6.6 10.8a15 15 0 006.6 6.6l2.2-2.2c.3-.3.7-.4 1-.2 1.1.4 2.3.6 3.6.6.6 0 1 .4 1 1V20c0 .6-.4 1-1 1A17 17 0 013 4c0-.6.4-1 1-1h3.5c.6 0 1 .4 1 1 0 1.3.2 2.5.6 3.6.1.3 0 .7-.2 1z"/></svg>5558130467</li>
      <li><svg viewBox="0 0 24 24"><circle cx="12" cy="12" r="10"/></svg>Stonedorf_Bzq</li>
      <li><svg viewBox="0 0 24 24"><path d="M2 5h20v14H2z M2 5l10 8 10-8" /></svg>Stonedorfdev@mailbox.example</li>
    </ul>
  </section>

  <section class="card card--realty" aria-label="Marek Tove realty business card">
    <div class="emboss-mark" aria-hidden="true"></div>
    <div class="brand">Marek Tove</div>
    <div class="identity">
      <span class="identity__bar"></span>
      <p class="name"><span class="name__first">Marek</span> <span class="name__last">Tove</span></p>
      <p class="role">Director</p>
    </div>
    <ul class="contacts">
      <li><svg viewBox="0 0 24 24"><path d="M6.6 10.8a15 15 0 006.6 6.6l2.2-2.2c.3-.3.7-.4 1-.2 1.1.4 2.3.6 3.6.6.6 0 1 .4 1 1V20c0 .6-.4 1-1 1A17 17 0 013 4c0-.6.4-1 1-1h3.5c.6 0 1 .4 1 1 0 1.3.2 2.5.6 3.6.1.3 0 .7-.2 1z"/></svg>5558130467</li>
      <li><svg viewBox="0 0 24 24"><circle cx="12" cy="12" r="10"/></svg>marekt</li>
      <li><svg viewBox="0 0 24 24"><circle cx="12" cy="12" r="10"/></svg>Marek_Bzq_Realtor</li>
      <li><svg viewBox="0 0 24 24"><path d="M2 5h20v14H2z M2 5l10 8 10-8"/></svg>Marek@Marektove.example</li>
      <li><svg viewBox="0 0 24 24"><path d="M12 2a10 10 0 100 20 10 10 0 000-20zm0 2c1.2 1.5 2 3.8 2.2 7H9.8C10 7.8 10.8 5.5 12 4zM9.8 13h4.4c-.2 3.2-1 5.5-2.2 7-1.2-1.5-2-3.8-2.2-7zM4.1 11a8 8 0 013.9-6c-.8 1.6-1.2 3.6-1.3 6zm0 2h2.6c.1 2.4.5 4.4 1.3 6a8 8 0 01-3.9-6zm15.8 0a8 8 0 01-3.9 6c.8-1.6 1.2-3.6 1.3-6zm0-2h-2.6c-.1-2.4-.5-4.4-1.3-6a8 8 0 013.9 6z"/></svg>www.marektove.example</li>
      <li><svg viewBox="0 0 24 24"><path d="M12 2a7 7 0 00-7 7c0 5 7 13 7 13s7-8 7-13a7 7 0 00-7-7zm0 9.5A2.5 2.5 0 1112 6.5a2.5 2.5 0 010 5z"/></svg>3847 61 St Nw</li>
    </ul>
  </section>

</main>
</body>
</html>
```